Process Serving Company needs a letterhead design

Looking to have a letterhead designed for letters to attorneys advertising our business. We would like something eye catching but professional. Colors and logos are attached. Please add "Process Service and Attorney Support" near the logo or header

Target Market(s)

Attorneys

Font styles to use
Serif
Sans Serif

Colors
33a6d7
0255a3
85cae6
cee9f5
ecf7fb

```html
<!DOCTYPE html>
<html lang="en">
<head>
<meta charset="utf-8">
<title>Desert Swift Serve Letterhead</title>
<link href="https://fonts.googleapis.com/css2?family=PT+Sans:wght@400;700&family=Arimo:wght@700&display=swap" rel="stylesheet">
<style>
  :root {
    --brand-blue: #26a5d9;
    --brand-deep: #0255a3;
    --brand-light: #85cae6;
    --brand-pale: #cee9f5;
    --ink: #3a3a3a;
    --ink-dark: #1a1a1a;
    --paper: #ffffff;
    --backdrop: #ececec;
    --signature-tone: #e4e4e4;
  }
  html, body {
    margin: 0;
    padding: 0;
    width: 1059px;
    height: 1200px;
    overflow: hidden;
    background: var(--backdrop);
  }
  .canvas {
    position: relative;
    width: 1059px;
    height: 1200px;
  }
  .letterhead {
    position: absolute;
    left: 105px;
    top: 0;
    width: 924px;
    height: 1305px;
    background: var(--paper);
    transform: scale(0.9195);
    transform-origin: top left;
    font-family: "PT Sans", sans-serif;
    color: var(--ink);
    overflow: hidden;
  }
  .header-waves {
    position: absolute;
    left: 0;
    top: 0;
    width: 924px;
    height: 220px;
  }
  .brand {
    position: absolute;
    left: 100px;
    top: 98px;
  }
  .brand-name {
    display: flex;
    align-items: center;
    gap: 14px;
    font-size: 30px;
    font-weight: 400;
    letter-spacing: 1px;
    line-height: 36px;
    color: var(--brand-blue);
    text-transform: uppercase;
  }
  .brand-mark {
    width: 22px;
    height: 22px;
    background: var(--brand-blue);
  }
  .brand-tagline {
    margin-top: 6px;
    padding-left: 36px;
    font-size: 14px;
    letter-spacing: 0.6px;
    color: var(--brand-deep);
  }
  .header-address {
    position: absolute;
    left: 712px;
    top: 61px;
    color: var(--paper);
    font-size: 15.5px;
    line-height: 21px;
  }
  .header-address strong {
    display: block;
    font-weight: 700;
  }
  .salutation {
    position: absolute;
    left: 58px;
    top: 281px;
    margin: 0;
    font-family: "Arimo", sans-serif;
    font-weight: 700;
    font-size: 19.5px;
    color: var(--ink-dark);
  }
  .letter-body {
    position: absolute;
    left: 59px;
    top: 333px;
    width: 805px;
  }
  .letter-body p {
    margin: 0 0 24.3px;
    font-size: 18.9px;
    line-height: 24.3px;
    text-align: justify;
  }
  .signature {
    position: absolute;
    left: 58px;
    top: 965px;
    width: 148px;
    height: 72px;
    background: var(--signature-tone);
    border-radius: 4px;
  }
  .footer-contacts {
    position: absolute;
    left: 70px;
    top: 1273px;
    display: flex;
    align-items: center;
    gap: 8px;
    font-size: 13px;
    color: var(--ink);
  }
  .footer-contacts .item {
    display: flex;
    align-items: center;
    gap: 4px;
  }
  .footer-contacts svg {
    width: 11px;
    height: 11px;
    fill: var(--brand-deep);
  }
  .footer-bar {
    position: absolute;
    left: 0;
    top: 1276px;
    width: 924px;
    height: 29px;
  }
  .footer-url {
    position: absolute;
    left: 713px;
    top: 1282px;
    color: var(--paper);
    font-weight: 700;
    font-size: 13.5px;
    letter-spacing: 0.6px;
  }
</style>
</head>
<body>
<div class="canvas">
  <div class="letterhead">
    <svg class="header-waves" viewBox="0 0 924 220" aria-hidden="true">
      <path fill="var(--brand-blue)" d="M0 0 H924 V121 C895 152 840 163 790 162 C830 170 855 174 872 178 C800 192 700 182 600 160 C480 130 380 58 250 52 C150 48 60 110 0 200 Z"/>
      <path fill="var(--paper)" d="M93 61 C150 20 260 10 380 38 C500 66 620 130 740 152 C800 162 845 166 872 166 C820 172 770 166 720 158 C600 138 500 80 380 60 C280 44 180 42 93 61 Z"/>
    </svg>

    <div class="brand">
      <div class="brand-name"><span class="brand-mark"></span>Desert Swift Serve</div>
      <div class="brand-tagline">Process Service and Attorney Support</div>
    </div>

    <div class="header-address">
      <strong>Desert Swift Serve</strong>
      4120 E Palo Verde Rd #208<br>
      Mesa AZ 85201
    </div>

    <h1 class="salutation">Dear Mr. Carter,</h1>

    <div class="letter-body">
      <p>Lorem Ipsum is simply dummy text of the printing and typesetting industry. Lorem Ipsum has been the industry's standard dummy text ever since the 1500s, when an unknown printer took a galley of type and scrambled it to make a type specimen book. It has survived not only five centuries, but also the leap into electronic typesetting, remaining essentially unchanged.</p>
      <p>The standard chunk of Lorem Ipsum used since the 1500s is reproduced below for those interested. Sections 1.10.32 and 1.10.33 from "de Finibus Bonorum et Malorum" by Cicero are also reproduced in their exact original form, accompanied by English versions from the 1914 translation by H. Rackham</p>
      <p>Lorem Ipsum is simply dummy text of the printing and typesetting industry. Lorem Ipsum has been the industry's standard dummy text ever since the 1500s, when an unknown printer took a galley of type and scrambled it to make a type specimen book. It has survived not only five centuries, but also the leap into electronic typesetting, remaining essentially unchanged. It was popularised in the</p>
      <p>The standard chunk of Lorem Ipsum used since the 1500s is reproduced below for those interested. Sections 1.10.32 and 1.10.33 from "de Finibus Bonorum et Malorum" by Cicero are also reproduced in their exact original form, accompanied by English versions from the 1914 translation by H. Rackham</p>
      <p>The standard chunk of Lorem Ipsum used since the 1500s is reproduced below for those interested. Sections 1.10.32 and 1.10.33 from "de Finibus Bonorum et Malorum" by Cicero are also reproduced in their exact original form.</p>
    </div>

    <div class="signature" role="img" aria-label="Handwritten signature of the sender"></div>

    <svg class="footer-bar" viewBox="0 0 924 29" preserveAspectRatio="none" aria-hidden="true">
      <rect x="0" y="16" width="660" height="5" fill="var(--brand-light)"/>
      <path fill="var(--brand-blue)" d="M660 29 C672 12 685 2 705 1 H924 V29 Z"/>
    </svg>

    <div class="footer-contacts">
      <span class="item">
        <svg viewBox="0 0 12 12"><path d="M3 1 L5 3.5 L4 5 C4.8 6.6 5.6 7.4 7 8 L8.5 7 L11 9 L9.5 11 C5 10.5 1.5 7 1 2.5 Z"/></svg>480-555-0142
      </span>
      <span class="item">
        <svg viewBox="0 0 12 12"><rect x="3" y="1" width="6" height="3"/><rect x="1" y="4.5" width="10" height="5" rx="1"/><rect x="3" y="8" width="6" height="3"/></svg>480-555-0143
      </span>
      <span class="item">
        <svg viewBox="0 0 12 12"><path d="M1 2.5 H11 V9.5 H1 Z M1.8 3.2 L6 6.5 L10.2 3.2"/></svg>hello@SwiftServeAZ.com
      </span>
      <span class="item">
        <svg viewBox="0 0 12 12"><circle cx="6" cy="6" r="5"/></svg>
      </span>
    </div>

    <div class="footer-url">www.SwiftServeAZ.com</div>
  </div>
</div>
</body>
</html>
```